Home Page for a Swiss based start up company, trading Natural & Health food ingredients (B2B)

I would like to create a home page for my new start up company (Veltrana Swiss AG), the main field of activity is the trading and marketing of Natural and Health food ingredients towards the functional Food and Food supplements industry. (B2B).
Target Market : Functional Food and Food Supplement Manufacturers (B2B) based in Switzerland and Europe
The values I would like to convey are :
- sourcing of natural and health ingredients, (example : natural plant extracts, Omega 3, plant proteins, natural vitamins, vegan food ingredients...etc)
- Health & Nutritional Health
- Eco-friendly and Sustainability
- High Quality Standard in term of products and logistic services
- Trust and reliability
- Flexibility & speed to market
-Technical advice for the development of new products

The site will be translated in 3 languages (German, French, English)
Number of web pages : 5 : Home, About us, Products, Our Services, Contact

See here below attached Logo file.

Here some link of websites which can be taken as benchmark or source of inspiration
- https://quorbelix.com
- https://www.dralvimo.com/

Target Market(s)

Manufacturers of Functional Foods and Food Supplements in Switzerland and Europe (B2B)

Industry/Entity Type

B2B Trading of Natural & Health Ingredients

Coding

Number of Pages Required

Font styles to use
Sans Serif

Colors
0054AA
0677BA
7BADD7
CADEEF
E8F1F8
0094D4
00A9DD
6FCCEA
C7EBF8
E9F6FB
00AB8E
00BBA5
67D7C9
C6EFE9
E9F9F6
59FF00
82FF00
B8FF75
E3FFCB
F4FFEA
FFF300
FFF600
FEFA6F
FFFEC7
FFFEE8
FFC000
F8CF3A
FAE287
FDF2CF
FEFAEE
F0912C
F2A743
F7CA91
FBE8D2
FDF5EE
EE7325
F08F49
F5BC92
FAE3D3
FDF4ED

Requirements
Must have
• inspiration towards nature, sustainability, vegan food, functional food & beverages, food supplements, nutritional health, low carbon footprint
Should not have
• animals, chemistry, food additives

```html
<!DOCTYPE html>
<html lang="en">
<head>
<meta charset="utf-8">
<title>Veltrana Swiss – Natural &amp; Health Ingredients</title>
<link href="https://fonts.googleapis.com/css2?family=Poppins:wght@400;500;600;700;800&family=Inter:wght@400;500;600&display=swap" rel="stylesheet">
<style>
:root{
  --orange:#EE7325;
  --orange-soft:#F08F49;
  --green:#1E9E7B;
  --green-deep:#17906F;
  --ink:#1c1c1c;
  --text:#555;
  --muted:#8a8a8a;
  --line:#d9d9d9;
  --paper:#f1f1f1;
  --white:#fff;
  --black:#000;
}
*{margin:0;padding:0;box-sizing:border-box}
html,body{width:1200px;height:3710px;overflow:hidden}
body{position:relative;background:var(--white);font-family:"Inter",Arial,sans-serif;color:var(--ink)}
.abs{position:absolute}

/* top bar */
.topbar-phone{left:111px;top:22px;font-size:17px;color:var(--orange);display:flex;align-items:center;gap:8px}
.topbar-sep{left:298px;top:22px;width:1px;height:20px;background:var(--line)}
.search{left:314px;top:16px;width:234px;height:35px;background:#f0f0f0;border-radius:3px;font-size:15px;color:#aaa;padding:8px 12px}
.search svg{position:absolute;right:11px;top:10px}
.lang{left:845px;top:22px;font-size:15px;font-weight:600;display:flex;align-items:center;gap:6px}
.social-top{top:13px;width:40px;height:40px;border:2px solid var(--green);border-radius:50%;display:flex;align-items:center;justify-content:center}
.social-top::after{content:"";width:10px;height:10px;border-radius:50%;background:var(--green)}
.logo{font-family:"Poppins",Arial,sans-serif;font-weight:600;font-size:33px;color:var(--ink);letter-spacing:-.5px}
.nav{top:88px;font-size:15px;font-weight:500;color:var(--ink)}
.nav.active{color:var(--green)}
.btn{background:var(--orange);color:var(--white);font-family:"Poppins",Arial,sans-serif;font-weight:600;font-size:15px;border-radius:4px;display:flex;align-items:center;justify-content:center}

/* hero */
.hero{left:0;top:143px;width:1200px;height:721px;background:radial-gradient(circle at 78% 40%,#6c8a3a 0,#3f5730 22%,#2b3339 45%,#23292e 100%)}
.hero-kicker{left:111px;top:325px;font-family:"Poppins",Arial,sans-serif;font-size:33px;color:var(--white);letter-spacing:.5px}
.hero-title{left:108px;top:372px;font-family:"Poppins",Arial,sans-serif;font-weight:700;font-size:84px;line-height:1;color:var(--white);letter-spacing:1px}
.hero-text{left:111px;top:480px;width:470px;font-size:15px;line-height:25px;color:#eee}
.dots{left:575px;top:684px;display:flex;gap:7px;align-items:center}
.dot{width:11px;height:11px;border-radius:50%;background:var(--white)}
.dot.on{width:15px;height:15px;background:var(--orange);border:3px solid var(--white)}

.sec-title{font-family:"Poppins",Arial,sans-serif;font-weight:600;font-size:31px;color:var(--orange);border-left:3px solid var(--orange);padding-left:14px;line-height:1}

.frame{border:3px solid #dcdcdc}
.body-text{font-size:14.5px;line-height:25.6px;color:var(--text)}

.services{left:0;top:1477px;width:1200px;height:763px;background:linear-gradient(180deg,#23a583 0,#1e9a79 50%,#22a282 100%)}
.card{top:1714px;width:308px;height:437px;background:var(--white);border-radius:4px;overflow:hidden;text-align:center}
.card-img{height:213px}
.card h3{font-family:"Poppins",Arial,sans-serif;font-weight:500;font-size:28px;margin-top:30px;color:var(--ink)}
.card p{font-size:14.5px;line-height:25.6px;color:var(--text);margin:16px 30px 0}
.card a{display:block;margin-top:16px;font-family:"Poppins",Arial,sans-serif;font-weight:500;font-size:15px;color:var(--orange);text-decoration:none}

.value{top:2410px;width:200px;text-align:center}
.value-ring{width:103px;height:103px;margin:0 auto;border:2px solid var(--green);border-radius:50%;display:flex;align-items:center;justify-content:center}
.value-ring.on{background:var(--green)}
.value span{display:block;margin-top:20px;font-size:17px;color:var(--ink)}
.value span.on{color:var(--green)}
.arrow{top:2468px;width:28px;height:28px;border-radius:50%;display:flex;align-items:center;justify-content:center}

.news-band{left:0;top:2661px;width:1200px;height:760px;background:var(--paper)}
.news{top:2811px;width:315px}
.news-img{height:196px}
.date{position:absolute;left:28px;top:177px;background:var(--orange);color:var(--white);font-size:13px;padding:11px 14px}
.news h4{margin-top:55px;font-family:"Poppins",Arial,sans-serif;font-weight:500;font-size:19px;line-height:29px;letter-spacing:-.2px;color:var(--ink)}
.news p{margin-top:8px;font-size:14.5px;line-height:25.6px;color:var(--muted)}
.news a{display:block;margin-top:12px;font-family:"Poppins",Arial,sans-serif;font-weight:600;font-size:15px;color:var(--orange);text-decoration:none}

.footer{left:0;top:3360px;width:1200px;height:350px;background:var(--black)}
.f-head{top:3425px;font-family:"Poppins",Arial,sans-serif;font-weight:600;font-size:18px;color:var(--white)}
.f-links{left:395px;top:3473px;list-style:none;font-size:15px;line-height:25.6px;color:var(--white)}
.f-item{left:585px;font-size:15px;line-height:25.6px;color:var(--white);display:flex;gap:12px}
.f-social{top:3544px;width:40px;height:40px;border-radius:50%;background:var(--white);display:flex;align-items:center;justify-content:center}
.f-social::after{content:"";width:10px;height:10px;border-radius:50%;background:var(--green)}
.newsletter{left:863px;top:3475px;width:224px;height:40px;background:var(--white);border:1px solid #ccc;border-radius:3px;font-size:14px;color:#888;padding:11px 12px}
.newsletter-btn{left:1035px;top:3475px;width:52px;height:40px;background:var(--green);border-radius:0 3px 3px 0;display:flex;align-items:center;justify-content:center}
.copy{left:0;top:3648px;width:1200px;text-align:center;font-size:15px;color:var(--white)}
</style>
</head>
<body>

<div class="abs topbar-phone">
  <svg width="16" height="16" viewBox="0 0 24 24"><path fill="#EE7325" d="M6.6 10.8a15.5 15.5 0 0 0 6.6 6.6l2.2-2.2c.3-.3.7-.4 1-.2 1.1.4 2.3.6 3.6.6.6 0 1 .4 1 1V20c0 .6-.4 1-1 1A17 17 0 0 1 3 4c0-.6.4-1 1-1h3.5c.6 0 1 .4 1 1 0 1.3.2 2.5.6 3.6.1.3 0 .7-.2 1z"/></svg>
  +41 (44) 555 0192
</div>
<div class="abs topbar-sep"></div>
<div class="abs search">Search
  <svg width="14" height="14" viewBox="0 0 24 24"><circle cx="10" cy="10" r="7" fill="none" stroke="#999" stroke-width="2.5"/><path d="M15 15l6 6" stroke="#999" stroke-width="2.5"/></svg>
</div>
<div class="abs lang">
  <svg width="18" height="18" viewBox="0 0 24 24"><circle cx="12" cy="12" r="10" fill="#1E9E7B"/></svg>
  ENG
  <svg width="10" height="6" viewBox="0 0 10 6"><path d="M0 0h10L5 6z" fill="#1c1c1c"/></svg>
</div>
<div class="abs social-top" style="left:942px" aria-label="Social profile"></div>
<div class="abs social-top" style="left:994px" aria-label="Social profile"></div>
<div class="abs social-top" style="left:1044px" aria-label="Social profile"></div>

<div class="abs logo" style="left:111px;top:77px">Veltrana Swiss</div>
<div class="abs nav active" style="left:454px">HOME</div>
<div class="abs nav" style="left:546px">ABOUT</div>
<div class="abs nav" style="left:645px">SERVICES</div>
<div class="abs nav" style="left:766px">VALUES</div>
<div class="abs nav" style="left:871px">BLOG</div>
<div class="abs btn" style="left:976px;top:76px;width:111px;height:45px">LOG IN</div>

<div class="abs hero" role="img" aria-label="Overhead photo of a fresh green salad bowl with seeds and leafy vegetables on a dark stone table"></div>
<svg class="abs" style="left:0;top:720px" width="1200" height="150" viewBox="0 0 1200 150" preserveAspectRatio="none">
  <path fill="#fff" d="M0 80 L60 70 L120 88 L190 62 L260 78 L320 55 L380 72 L450 50 L520 66 L600 44 L680 70 L740 48 L800 64 L880 52 L950 68 L1020 46 L1100 60 L1160 50 L1200 58 L1200 150 L0 150Z"/>
</svg>
<div class="abs hero-kicker">WWLCOME TO</div>
<div class="abs hero-title">VELTRANA SWISS</div>
<div class="abs hero-text">Lorem ipsum dolor sit amet, consectetur adipiscing elit, sed do eiusmod tempor incididunt ut labore et dolore magna aliqua.</div>
<div class="abs btn" style="left:111px;top:556px;width:137px;height:44px">GET STARTED</div>
<div class="abs dots"><span class="dot"></span><span class="dot on"></span><span class="dot"></span></div>

<div class="abs frame" style="left:108px;top:906px;width:233px;height:422px"></div>
<div class="abs" style="left:111px;top:916px;width:222px;height:407px;background:linear-gradient(160deg,#c9c3bb,#e8c15a 55%,#f2f0ec)" role="img" aria-label="Plant-based supplement capsules in white spoons"></div>
<div class="abs frame" style="left:333px;top:955px;width:265px;height:418px"></div>
<div class="abs" style="left:341px;top:955px;width:248px;height:410px;background:linear-gradient(160deg,#4f7d2c,#8a9d3a 40%,#c44a3a 70%,#3e6a2b)" role="img" aria-label="Fresh vegetables including corn, radishes and leeks"></div>

<div class="abs sec-title" style="left:657px;top:913px">About Veltrana Swiss</div>
<p class="abs body-text" style="left:657px;top:969px;width:432px">Lorem ipsum dolor sit amet, consectetur adipiscing elit, se do eiusmod tempor incididunt ut labore et dolore magna aliqu Ut enim ad minim veniam, quis nostrud exercitation ulla lab ni ut aliquip ex ea commodo consequat. Duis aute ir reprehenderit in voluptate velit esse cillum dolore eu fugiat nulla Excepteur sint occaecat cupidatat non proident, sunt in culpa des mollit anim id est laborum.</p>
<p class="abs body-text" style="left:657px;top:1169px;width:432px">Lorem ipsum dolor sit amet, consectetur adipiscing elit, se do eiusmod tempor incididunt ut labore et dolore magna aliqu Ut enim ad minim veniam, quis nostrud exercitation ulla lab ni ut aliquip ex ea commodo consequat.</p>
<div class="abs btn" style="left:657px;top:1299px;width:137px;height:44px;font-size:14px">LERAN MORE</div>
<div class="abs" style="left:1022px;top:1253px;width:178px;height:224px;background:linear-gradient(180deg,#fff 0,#f3e6a2 45%,#d9b550 85%,#a9782f)" role="img" aria-label="Glasses of lemonade with mint and lemon slices"></div>

<div class="abs services" role="img" aria-label="Soft green background showing fresh leaves"></div>
<div class="abs sec-title" style="left:496px;top:1566px;color:#fff;border-color:#fff">Our Services</div>
<p class="abs" style="left:340px;top:1619px;width:520px;text-align:center;font-size:15px;line-height:25.6px;color:#fff">Lorem ipsum dolor sit amet, consectetur adipiscing elit, sed do eiusmod tempor incididunt ut labore et dolore magna aliqua.</p>

<div class="abs card" style="left:111px">
  <div class="card-img" style="background:linear-gradient(135deg,#9a9d9f,#d8dadb 50%,#6e7275)" role="img" aria-label="Food scientist with a tablet in a production facility"></div>
  <h3>Lorem ipsum</h3>
  <p>Lorem ipsum dolor sit amet, consectetur adipiscing elit, sed do eiusmod tempor incididunt ut</p>
  <a href="#">Learn More</a>
</div>
<div class="abs card" style="left:446px">
  <div class="card-img" style="background:linear-gradient(135deg,#3c4a2a,#b8964e 55%,#6d5a3a)" role="img" aria-label="Farmer harvesting fresh beetroot in a field"></div>
  <h3>Lorem ipsum</h3>
  <p>Lorem ipsum dolor sit amet, consectetur adipiscing elit, sed do eiusmod tempor incididunt ut</p>
  <a href="#">Learn More</a>
</div>
<div class="abs card" style="left:780px">
  <div class="card-img" style="background:linear-gradient(135deg,#ef7a22,#f49a3c 50%,#d8601a)" role="img" aria-label="Carrots being sorted on a processing line"></div>
  <h3>Lorem ipsum</h3>
  <p>Lorem ipsum dolor sit amet, consectetur adipiscing elit, sed do eiusmod tempor incididunt ut</p>
  <a href="#">Learn More</a>
</div>

<div class="abs sec-title" style="left:516px;top:2327px">Our Value</div>
<div class="abs arrow" style="left:70px;border:2px solid var(--orange)">
  <svg width="10" height="10" viewBox="0 0 10 10"><path d="M7 1L3 5l4 4" fill="none" stroke="#EE7325" stroke-width="1.6"/></svg>
</div>
<div class="abs arrow" style="left:1099px;border:1.5px solid #888">
  <svg width="10" height="10" viewBox="0 0 10 10"><path d="M3 1l4 4-4 4" fill="none" stroke="#666" stroke-width="1.6"/></svg>
</div>

<div class="abs value" style="left:96px">
  <div class="value-ring"><svg width="46" height="46" viewBox="0 0 46 46" fill="none" stroke="#1E9E7B" stroke-width="2"><rect x="8" y="6" width="24" height="32" rx="2"/><path d="M14 14h12M14 20h12M14 26h6"/><circle cx="33" cy="33" r="7"/></svg></div>
  <span>Health &amp; Nutritional</span>
</div>
<div class="abs value" style="left:299px">
  <div class="value-ring on"><svg width="46" height="46" viewBox="0 0 46 46" fill="none" stroke="#fff" stroke-width="2"><path d="M10 34C10 18 22 10 36 10c0 16-10 24-26 24z"/><path d="M10 34l16-16"/></svg></div>
  <span class="on">Eco-friendly</span>
</div>
<div class="abs value" style="left:500px">
  <div class="value-ring"><svg width="46" height="46" viewBox="0 0 46 46" fill="none" stroke="#1E9E7B" stroke-width="2"><path d="M23 6l14 5v11c0 9-6 15-14 18-8-3-14-9-14-18V11z"/><path d="M16 23l5 5 9-10"/></svg></div>
  <span>Trust and reliability</span>
</div>
<div class="abs value" style="left:702px">
  <div class="value-ring"><svg width="46" height="46" viewBox="0 0 46 46" fill="none" stroke="#1E9E7B" stroke-width="2"><rect x="6" y="14" width="22" height="16"/><path d="M28 19h7l5 6v5H28z"/><circle cx="14" cy="32" r="3"/><circle cx="34" cy="32" r="3"/></svg></div>
  <span>Speed to market</span>
</div>
<div class="abs value" style="left:904px">
  <div class="value-ring"><svg width="46" height="46" viewBox="0 0 46 46" fill="none" stroke="#1E9E7B" stroke-width="2"><circle cx="23" cy="23" r="16"/><path d="M23 14l8 4.5v9L23 32l-8-4.5v-9z"/></svg></div>
  <span>Security of supply</span>
</div>

<div class="abs news-band"></div>
<div class="abs sec-title" style="left:111px;top:2746px">Latest News</div>

<div class="abs news" style="left:111px">
  <div class="news-img" style="background:linear-gradient(160deg,#2e4a1f,#6a8f3a 50%,#24361a)" role="img" aria-label="Forest canopy seen from below"></div>
  <div class="date">27 April,2022</div>
  <h4>Sed ut perspiciatis unde omnis iste natus error sit voluptatem</h4>
  <p>Lorem ipsum dolor sit amet, consectetur adipiscing elit, sed do eiusmod tempor</p>
  <a href="#">READ MORE</a>
</div>
<div class="abs news" style="left:442px">
  <div class="news-img" style="background:radial-gradient(circle at 50% 55%,#cfd8cc 0,#4f8a2e 40%,#2f5a1c)" role="img" aria-label="Aerial view of green forest treetops"></div>
  <div class="date">27 April,2022</div>
  <h4>Sed ut perspiciatis unde omnis iste natus error sit voluptatem</h4>
  <p>Lorem ipsum dolor sit amet, consectetur adipiscing elit, sed do eiusmod tempor</p>
  <a href="#">READ MORE</a>
</div>
<div class="abs news" style="left:772px">
  <div class="news-img" style="background:linear-gradient(160deg,#e99436,#7c8f4a 55%,#b8c1a8)" role="img" aria-label="Orange tree with ripe fruit in an orchard"></div>
  <div class="date">27 April,2022</div>
  <h4>Sed ut perspiciatis unde omnis iste natus error sit voluptatem</h4>
  <p>Lorem ipsum dolor sit amet, consectetur adipiscing elit, sed do eiusmod tempor</p>
  <a href="#">READ MORE</a>
</div>

<svg class="abs" style="left:0;top:3228px" width="1200" height="140" viewBox="0 0 1200 140" preserveAspectRatio="none">
  <path fill="#000" d="M0 100 L60 92 L110 104 L170 80 L200 60 L240 50 L270 22 L300 48 L340 40 L380 70 L430 58 L480 80 L540 66 L600 84 L650 62 L700 76 L760 54 L820 70 L880 58 L940 40 L990 62 L1040 52 L1090 74 L1150 64 L1200 72 L1200 140 L0 140Z"/>
</svg>
<div class="abs footer"></div>
<div class="abs logo" style="left:111px;top:3460px;color:#fff">Veltrana Swiss</div>
<div class="abs f-social" style="left:112px" aria-label="Social profile"></div>
<div class="abs f-social" style="left:167px" aria-label="Social profile"></div>
<div class="abs f-social" style="left:222px" aria-label="Social profile"></div>
<div class="abs f-social" style="left:277px" aria-label="Social profile"></div>

<div class="abs f-head" style="left:395px">QUICK LINKS</div>
<ul class="abs f-links"><li>Home</li><li>About</li><li>Services</li><li>Values</li><li>Blog</li></ul>

<div class="abs f-head" style="left:585px">CONTACT US</div>
<div class="abs f-item" style="top:3479px">
  <svg width="16" height="20" viewBox="0 0 16 20"><path fill="#fff" d="M8 0a8 8 0 0 0-8 8c0 6 8 12 8 12s8-6 8-12a8 8 0 0 0-8-8zm0 11a3 3 0 1 1 0-6 3 3 0 0 1 0 6z"/></svg>
  <span>Lorem ipsum dolor<br>sit amet</span>
</div>
<div class="abs f-item" style="top:3538px">
  <svg width="17" height="17" viewBox="0 0 24 24"><path fill="#fff" d="M6.6 10.8a15.5 15.5 0 0 0 6.6 6.6l2.2-2.2c.3-.3.7-.4 1-.2 1.1.4 2.3.6 3.6.6.6 0 1 .4 1 1V20c0 .6-.4 1-1 1A17 17 0 0 1 3 4c0-.6.4-1 1-1h3.5c.6 0 1 .4 1 1 0 1.3.2 2.5.6 3.6.1.3 0 .7-.2 1z"/></svg>
  <span>+41 (44) 555 0192</span>
</div>
<div class="abs f-item" style="top:3575px">
  <svg width="17" height="14" viewBox="0 0 17 14" style="margin-top:6px"><rect width="17" height="14" rx="1" fill="#fff"/><path d="M1 1l7.5 6L16 1" fill="none" stroke="#000" stroke-width="1.5"/></svg>
  <span>info@veltranaswiss.com</span>
</div>

<div class="abs f-head" style="left:863px">NEWSLETTER</div>
<div class="abs newsletter">Ener email</div>
<div class="abs newsletter-btn">
  <svg width="17" height="14" viewBox="0 0 17 14"><rect width="17" height="14" rx="1" fill="#fff"/><path d="M1 1l7.5 6L16 1" fill="none" stroke="#1E9E7B" stroke-width="1.5"/></svg>
</div>

<div class="abs copy">©Copyrights 2022 Veltrana Swiss &nbsp;| &nbsp;&nbsp;All Rights Reserved</div>

</body>
</html>
```